Sophisticated, clean website reflecting my feminine, playful side to sell my abstract art,

I need a website no more than 3 pages to showcase my paintings, a little about me and some contact info. I do abstracts so looking for something a little edgy, yet feminine and current.
Updates

Hi there, These are some artists websites that I Iike: Marnelvoss.com (I like how airy it is) peterwallombry.com garethpolvens.com (I like how it scrolls) I'll need a place for a photo ( a headshot-i do not have it yet so I'll need to be able to upload that later) as well as an area for my bio. Also, it's important that I will be able to upload any new photos and descriptions easily so it should be user friendly. Lastly, I like in a sunny place so would like to have this seem upbeat and playful as that is how i like to paint. thanks-I'm trying to upload my photos now -

Target Market(s)

ppl ages 35-70 who want large scale art for their homes

Industry/Entity Type

art

Coding

Coded - Design and coding required

Number of Pages Required

3 page

Colors

Designer to choose colors to be used in the design.

Requirements
Must have
• photos of my art, a place for my bio, be easy to reach me. tasteful-nothing too "in your face" -my clients are pretty high end and organized. They like clean lines
Nice to have
• sophisticated background, muted tones in the back-similar clean font throughout-no cursive
Should not have
• too many dark areas. Too many blocks of color. Too serious.

```html
<!DOCTYPE html>
<html lang="en">
<head>
<meta charset="utf-8">
<title>Helena Marsh Art</title>
<link href="https://fonts.googleapis.com/css2?family=Cinzel:wght@400;600&family=Open+Sans:ital,wght@0,400;0,600;1,400&display=swap" rel="stylesheet">
<style>
:root{
  --orange:#f47a1f;
  --blue:#3f7fbb;
  --blue-dark:#2f6aa3;
  --olive:#a7a62c;
  --ink:#222;
  --muted:#666;
  --band:#ececec;
  --topbar:#e9e9e9;
  --white:#fff;
}
*{margin:0;padding:0;box-sizing:border-box}
html,body{width:1200px;height:2984px;overflow:hidden}
body{position:relative;background:var(--white);font-family:"Open Sans",Arial,sans-serif;color:var(--ink)}
.abs{position:absolute}
.display{font-family:"Cinzel",Georgia,serif}

.topbar{left:0;top:0;width:1200px;height:34px;background:var(--topbar);text-align:center;font-style:italic;font-size:13px;line-height:34px;color:#444}
.header{left:0;top:34px;width:1200px;height:156px}
.logo{left:0;top:28px;width:1200px;text-align:center;font-family:"Cinzel",Georgia,serif;font-size:30px;color:var(--orange);letter-spacing:1px}
.nav{left:0;top:100px;width:1200px;display:flex;justify-content:center;align-items:center;gap:52px;font-family:"Cinzel",Georgia,serif;font-size:15px;font-weight:600;color:#333}
.nav .active{border-bottom:2px solid var(--orange);padding-bottom:4px}

.hero{left:0;top:190px;width:1200px;height:560px;display:flex;gap:4px;background:var(--white)}
.hero-panel{flex:1;height:100%}
.p1{background:linear-gradient(160deg,#f6913d,#f07222 60%,#e8681a)}
.p2{background:linear-gradient(160deg,#5b8fc6,#3a72b0 55%,#5586bb)}
.p3{background:linear-gradient(160deg,#c1bb3a,#9ea12c 55%,#b6ae3a)}
.hero-text{left:0;top:370px;width:1200px;text-align:center;color:var(--white);font-family:"Cinzel",Georgia,serif}
.hero-text .small{font-size:52px;letter-spacing:2px}
.hero-text .big{font-size:74px;margin-top:2px}
.btn{display:inline-block;background:var(--orange);color:var(--white);border-radius:30px;font-family:"Cinzel",Georgia,serif;font-weight:600}
.hero-btn{left:520px;top:558px;width:160px;height:54px;line-height:54px;text-align:center;font-size:20px}

.about-band{left:600px;top:872px;width:600px;height:428px;background:var(--band)}
.about-photo{left:0;top:832px;width:600px;height:490px;background:linear-gradient(135deg,#cfc6bb,#a89a8a 50%,#d8cfc3);box-shadow:0 6px 14px rgba(0,0,0,.25)}
.about-title{left:656px;top:890px;font-size:36px;color:#222}
.about-text{left:656px;top:955px;width:490px;font-size:13.5px;line-height:22px;color:var(--muted)}
.about-btn{left:656px;top:1200px;width:136px;height:40px;line-height:40px;text-align:center;font-size:14px}

.section-title{left:0;top:1400px;width:1200px;text-align:center;font-size:44px;font-weight:600;color:#111}
.work{width:320px}
.work .art{width:320px;height:320px}
.work .cap{margin-top:30px;text-align:center;font-family:"Cinzel",Georgia,serif;font-size:22px;font-weight:600;color:#222}

.contact{left:0;top:2356px;width:1200px;height:548px;background:linear-gradient(135deg,#4b89c2,#3a76b4 50%,#4a86bf)}
.footer{left:0;top:2904px;width:1200px;height:80px;background:var(--blue-dark);color:#dfe9f4;text-align:center;font-size:14px;line-height:80px}
.contact-title{left:100px;top:2440px;font-size:44px;color:var(--white)}
.info-row{left:100px;display:flex;align-items:center;gap:22px;color:var(--white);font-size:14px;line-height:22px}
.info-icon{width:34px;height:34px;border-radius:50%;background:var(--white);display:flex;align-items:center;justify-content:center;flex:none}
.social-label{left:100px;top:2770px;color:var(--white);font-size:15px;font-weight:600}
.social{left:100px;top:2805px;display:flex;gap:10px}
.social span{width:26px;height:26px;border-radius:50%;background:var(--orange)}

.form{left:462px;top:2430px;width:644px;height:440px;background:#f4f4f4;border-radius:10px;padding:34px 44px}
.form h3{font-family:"Cinzel",Georgia,serif;font-weight:400;font-size:30px;color:#333;margin-bottom:26px}
.fields{display:grid;grid-template-columns:1fr 1fr;gap:18px 24px}
.field{height:52px;background:var(--white);border:1px solid #ddd;border-radius:26px;font-size:12px;color:#777;padding:0 26px;line-height:52px}
.field.msg{grid-column:1/3;height:112px;border-radius:22px;line-height:20px;padding-top:16px}
.submit{margin-top:22px;width:96px;height:40px;line-height:40px;text-align:center;font-size:14px;border-radius:6px}
</style>
</head>
<body>

<div class="abs topbar">Lorem ipsum dolor sit amet, consectetur adipiscing elit, sed do eiusmod</div>

<header class="abs header">
  <div class="abs logo">Helena Marsh Art</div>
  <nav class="abs nav">
    <span class="active">Home</span>
    <span>About Me</span>
    <span>Abstracts</span>
    <span>Contact Us</span>
    <svg width="20" height="20" viewBox="0 0 20 20" aria-label="Cart"><path d="M1 3h3l2.5 10h10l2-7H5.5" fill="none" stroke="#f47a1f" stroke-width="2" stroke-linejoin="round"/><circle cx="8" cy="17" r="1.6" fill="#f47a1f"/><circle cx="15" cy="17" r="1.6" fill="#f47a1f"/></svg>
  </nav>
</header>

<section class="abs hero">
  <div class="hero-panel p1" role="img" aria-label="Orange abstract floral painting detail"></div>
  <div class="hero-panel p2" role="img" aria-label="Blue abstract brushstroke painting detail"></div>
  <div class="hero-panel p3" role="img" aria-label="Olive green abstract painting detail"></div>
</section>
<div class="abs hero-text">
  <div class="small">Welcome to</div>
  <div class="big">Helena Marsh Art</div>
</div>
<a class="abs btn hero-btn">Arts</a>

<section>
  <div class="abs about-band"></div>
  <div class="abs about-photo" role="img" aria-label="The artist smiling beside her easel in a paint-filled studio"></div>
  <h2 class="abs about-title display">About Me</h2>
  <p class="abs about-text">Sed ut perspiciatis unde omnis iste natus error sit voluptatem accusantium doloremque laudantium, totam rem aperiam, eaque ipsa quae ab illo inventore veritatis et quasi architecto beatae vitae dicta sunt explicabo. Nemo enim ipsam voluptatem quia voluptas sit aspernatur aut odit aut fugit, sed quia consequuntur magni dolores eos qui ratione voluptatem sequi nesciunt. Neque porro quisquam est, qui dolorem ipsum quia dolor sit amet, consectetur, adipisci velit, sed quia non numquam eius modi tempora incidunt ut labore et dolore magnam aliquam quaerat voluptatem.</p>
  <a class="abs btn about-btn">Learn More</a>
</section>

<section>
  <h2 class="abs section-title display">Abstracts Painting</h2>
  <div class="abs work" style="left:88px;top:1490px"><div class="art" role="img" aria-label="Abstract painting, pink and brown swirls" style="background:linear-gradient(135deg,#e9d6cf,#c98c86 50%,#e4c9b5)"></div><div class="cap">Golden Hour</div></div>
  <div class="abs work" style="left:432px;top:1490px"><div class="art" role="img" aria-label="Abstract painting, blue drips on white" style="background:linear-gradient(180deg,#d7dde3,#7aa0c0 45%,#eef0f2)"></div><div class="cap">Tidepool</div></div>
  <div class="abs work" style="left:776px;top:1490px"><div class="art" role="img" aria-label="Abstract painting, dark red and pink swirls" style="background:linear-gradient(135deg,#d9b9bf,#8a3a4a 50%,#c99aa2)"></div><div class="cap">Rumba Rose</div></div>
  <div class="abs work" style="left:88px;top:1894px"><div class="art" role="img" aria-label="Abstract painting, red loops on white" style="background:linear-gradient(135deg,#eee6e4,#a8303a 50%,#e8dcda)"></div><div class="cap">Off Kilter</div></div>
  <div class="abs work" style="left:432px;top:1894px"><div class="art" role="img" aria-label="Abstract painting, teal and orange burst" style="background:linear-gradient(135deg,#d9d5c9,#2e7a7a 45%,#c46a2c 70%,#e6e2d8)"></div><div class="cap">Breaking Borders</div></div>
  <div class="abs work" style="left:776px;top:1894px"><div class="art" role="img" aria-label="Abstract painting, brown and red floral shapes" style="background:linear-gradient(135deg,#eae4de,#6e3428 50%,#dcc8bc)"></div><div class="cap">Tango</div></div>
</section>

<section class="abs contact"></section>
<h2 class="abs contact-title display">Contact Info</h2>
<div class="abs info-row" style="top:2530px">
  <span class="info-icon"><svg width="14" height="16" viewBox="0 0 14 16"><path d="M7 1a5 5 0 0 0-5 5c0 4 5 9 5 9s5-5 5-9a5 5 0 0 0-5-5z" fill="#3f7fbb"/><circle cx="7" cy="6" r="1.8" fill="#fff"/></svg></span>
  <span>Lorem ipsum dolor sit amet, consectetur<br>adipiscing</span>
</div>
<div class="abs info-row" style="top:2610px">
  <span class="info-icon"><svg width="16" height="12" viewBox="0 0 16 12"><rect x="1" y="1" width="14" height="10" rx="1" fill="none" stroke="#3f7fbb" stroke-width="1.6"/><path d="M1 2l7 5 7-5" fill="none" stroke="#3f7fbb" stroke-width="1.6"/></svg></span>
  <span>info@helenamarshart.com</span>
</div>
<div class="abs info-row" style="top:2670px">
  <span class="info-icon"><svg width="14" height="14" viewBox="0 0 14 14"><path d="M3 1l2.5 3-1.5 1.5c.8 1.8 2 3 3.8 3.8L9.3 7.8 12.5 10 11 13C6 13 1 8 1 3z" fill="#3f7fbb"/></svg></span>
  <span>+1 000 000 0000</span>
</div>
<div class="abs social-label">SOCIAL MEDIA</div>
<div class="abs social" aria-label="Social links"><span></span><span></span><span></span><span></span><span></span></div>

<form class="abs form">
  <h3>Get In Touch</h3>
  <div class="fields">
    <div class="field">First Name*</div>
    <div class="field">Last Name*</div>
    <div class="field">Email*</div>
    <div class="field">Phone*</div>
    <div class="field msg">Tell us about your need *</div>
  </div>
  <div class="btn submit">Submit</div>
</form>

<footer class="abs footer">© Copyrights 2022 © Helena Marsh Art | All Rights Reserved</footer>

</body>
</html>
```